Business Card for Coastal Tundrabridge Advisory

We need a business card for Coastal Tundrabridge Advisory. The company website address is provided below. The company logo is attached. We provide specialized permafrost services to the mining, transportation, and oil & gas industries. The card should be prepared for:
Matthias Korhonen, PhD.
Coastal Tundrabridge Advisory
PO Box 418259
Quillwater, Alaska 99642
Direct: +1-907-555-0143
Email: mkorhonen@tundrabridgeadvisory.example
Website: www.coastaltundrabridgeadvisory.example

```html
<!DOCTYPE html>
<html lang="en">
<head>
<meta charset="utf-8">
<title>Coastal Tundrabridge Advisory – Business Card</title>
<link rel="stylesheet" href="https://fonts.googleapis.com/css2?family=Montserrat:wght@300;600&family=Roboto:wght@400;500&display=swap">
<style>
  :root {
    --backdrop: #232323;
    --card-navy: #111723;
    --pattern-blue: #2e93d6;
    --pattern-deep: #1a2a40;
    --ink-white: #f4f6f8;
    --ink-soft: #d9dee6;
  }
  * { margin: 0; padding: 0; box-sizing: border-box; }
  html, body {
    width: 1200px; height: 711px; overflow: hidden;
    background: var(--backdrop);
  }
  .stage {
    position: relative; width: 1200px; height: 711px;
    display: flex; align-items: center; justify-content: center; gap: 40px;
  }
  .card {
    position: relative; width: 540px; height: 309px;
    background: var(--card-navy); overflow: hidden;
    color: var(--ink-white);
  }
  /* Front */
  .front .pattern-field {
    position: absolute; inset: 0;
    background: linear-gradient(180deg, var(--pattern-blue) 0%, var(--pattern-deep) 40%, var(--card-navy) 75%);
    opacity: .55;
  }
  .front .brand {
    position: absolute; left: 0; right: 0; top: 112px; text-align: center;
    font-family: "Roboto", sans-serif; font-weight: 500;
    font-size: 24px; letter-spacing: 3px; text-transform: uppercase;
    color: var(--ink-white);
  }
  .front .services {
    position: absolute; left: 0; right: 0; bottom: 34px; text-align: center;
    font-family: "Roboto", sans-serif; color: var(--ink-soft);
  }
  .services-title { font-size: 10px; font-weight: 500; letter-spacing: .5px; margin-bottom: 4px; color: var(--ink-white); }
  .services-text { font-size: 10px; }
  /* Back */
  .back .brand {
    position: absolute; right: 26px; top: 34px;
    font-family: "Roboto", sans-serif; font-weight: 500;
    font-size: 19px; letter-spacing: 2px; text-transform: uppercase;
    color: var(--ink-white);
  }
  .back .contact {
    position: absolute; right: 26px; top: 120px; text-align: right;
    font-family: "Roboto", sans-serif; font-size: 11.5px; line-height: 17px;
    color: var(--ink-white); list-style: none;
  }
  .contact li { display: flex; justify-content: flex-end; align-items: center; gap: 7px; }
  .contact .icon { width: 11px; height: 11px; flex: none; }
  .contact .spacer { width: 11px; }
  .back .person {
    position: absolute; left: 22px; bottom: 22px;
    transform: rotate(-90deg); transform-origin: left bottom;
    translate: 62px 0;
    font-family: "Montserrat", sans-serif; white-space: nowrap;
  }
  .person-name { font-size: 27px; line-height: 30px; }
  .person-name .first { font-weight: 600; }
  .person-name .last { font-weight: 300; }
  .person-title { font-size: 13px; font-weight: 300; }
</style>
</head>
<body>
<main class="stage">
  <section class="card front">
    <div class="pattern-field" role="img" aria-label="Repeated company wordmark pattern fading from blue to navy"></div>
    <h1 class="brand">Coastal Tundrabridge Advisory</h1>
    <div class="services">
      <p class="services-title">OUR SERVICES</p>
      <p class="services-text">We provide specialized permafrost services to the mining, transportation, and oil &amp; gas industries</p>
    </div>
  </section>

  <section class="card back">
    <h2 class="brand">Coastal Tundrabridge Advisory</h2>
    <ul class="contact">
      <li>PO Box 418259<span class="spacer"></span></li>
      <li>Quillwater, Alaska 99642<span class="spacer"></span></li>
      <li>+1-907-555-0143
        <svg class="icon" viewBox="0 0 12 12"><circle cx="6" cy="6" r="6" fill="#f4f6f8"/><path d="M4 3.2l1 1.6-.6.7c.5 1 1.2 1.7 2.1 2.1l.7-.6 1.6 1-.5 1C5.9 9 3 6.1 3 3.7z" fill="#111723"/></svg>
      </li>
      <li>mkorhonen@tundrabridgeadvisory.example
        <svg class="icon" viewBox="0 0 12 12"><rect x="0.5" y="2" width="11" height="8" rx="1" fill="#f4f6f8"/><path d="M1 2.6L6 6.6l5-4" fill="none" stroke="#111723" stroke-width="1"/></svg>
      </li>
      <li>www.coastaltundrabridgeadvisory.example
        <svg class="icon" viewBox="0 0 12 12"><circle cx="6" cy="6" r="5.5" fill="#f4f6f8"/><g fill="none" stroke="#111723" stroke-width=".8"><ellipse cx="6" cy="6" rx="2.3" ry="5.2"/><path d="M.8 6h10.4M1.6 3.5h8.8M1.6 8.5h8.8"/></g></svg>
      </li>
    </ul>
    <div class="person">
      <p class="person-name"><span class="first">Matthias</span> <span class="last">Korhonen</span></p>
      <p class="person-title">PhD</p>
    </div>
  </section>
</main>
</body>
</html>
```